web page design with coding

We are a start up insurance agency who needs to design a full functional web page. we recently did a postcard design though drawkettle I will upload the final project for you to see the color scheme/font we would like to continue to use. I also have a rough draft of verbage I would like our website to have. I will upload that as well.

Reason: I am sorry but the person who will make the final decision on the website is out of the country at the moment and will make the final decision when he returns.

Industry/Entity Type

Insurance

Coding

Coded - Design and coding required

```html
<!DOCTYPE html>
<html lang="en">
<head>
<meta charset="utf-8">
<title>Corvella Insurance Group</title>
<link href="https://fonts.googleapis.com/css2?family=Montserrat:wght@400;500;600;700;800&display=swap" rel="stylesheet">
<style>
:root{
  --blue:#0b5d95;
  --blue-dark:#0a4f80;
  --heading:#0c5a8e;
  --link:#1a4f86;
  --green:#7b9a2c;
  --olive:#6b7a2a;
  --text:#3a3a3a;
  --muted:#666;
  --line:#d6d6d6;
  --white:#fff;
}
*{box-sizing:border-box;margin:0;padding:0}
html,body{width:1200px;height:2171px;overflow:hidden;background:var(--white)}
body{font-family:"Montserrat",Arial,sans-serif;color:var(--text);position:relative}
.abs{position:absolute}
.hero{left:0;top:0;width:1200px;height:620px;overflow:hidden}
.hero-photo{position:absolute;inset:0;background:linear-gradient(180deg,#cfe0ee 0%,#e8eef2 35%,#b9a58c 60%,#8a9a6a 80%,#7f9358 100%)}
.hero-waves{position:absolute;left:0;top:0}
.brand{left:135px;top:30px;display:flex;align-items:center;gap:10px}
.brand-mark{width:14px;height:14px;background:var(--heading)}
.brand-name{font-weight:700;font-size:17px;color:var(--heading);line-height:1}
.nav{left:557px;top:27px;display:flex;align-items:center;gap:0}
.nav a{font-size:12px;color:var(--blue);text-decoration:none;padding:7px 12px;margin-right:12px}
.nav a.active{background:var(--white)}
.nav .search{width:28px;height:28px;border-radius:50%;background:var(--white);display:flex;align-items:center;justify-content:center;margin-left:10px}
.callout{left:158px;top:350px;color:var(--white)}
.callout .lead{font-weight:700;font-size:14px}
.callout .sub{font-size:14px;margin-top:4px}
.callout .phone{font-weight:700;font-size:27px;margin-top:14px;display:flex;align-items:center;gap:12px}
.tilt{background:var(--white);padding:10px;box-shadow:0 4px 10px rgba(0,0,0,.35)}
.tilt div{width:100%;height:100%}
.tilt-family{left:540px;top:380px;width:272px;height:210px;transform:rotate(-8deg)}
.tilt-family div{background:linear-gradient(135deg,#f1e5da,#d7b9a0 60%,#9c8474)}
.tilt-car{left:805px;top:395px;width:258px;height:200px;transform:rotate(9deg)}
.tilt-car div{background:linear-gradient(135deg,#f3f3f3,#e1c9b8 55%,#2e6a3e)}
h2.section-title{font-weight:800;font-size:28px;color:var(--heading);letter-spacing:.3px}
p.copy{font-size:10.6px;line-height:19.2px;color:var(--text);letter-spacing:-.1px}
.welcome{left:162px;top:650px;width:556px}
.welcome .copy{margin-top:12px}
.btn{display:inline-block;background:var(--blue);color:var(--white);font-size:11px;padding:10px 14px;margin-top:24px;border:1px solid #074c7c}
.framed{background:var(--white);padding:8px;box-shadow:0 2px 6px rgba(0,0,0,.3)}
.framed div{width:100%;height:100%}
.photo-couple{left:763px;top:647px;width:280px;height:203px}
.photo-couple div{background:linear-gradient(135deg,#e9e4df,#c9b3a4 50%,#5b7fa6)}
.products{left:162px;top:900px;width:556px}
.products .copy{margin-top:14px}
.products .prompt{font-weight:600;font-size:12px;color:#222;margin-top:18px}
.tabs{display:flex;gap:8px;margin-top:14px}
.tab{width:193px;height:39px;display:flex;align-items:center;justify-content:center;font-weight:600;font-size:15px}
.tab.outline{border:1px solid var(--line);color:var(--blue);position:relative}
.tab.outline::after{content:"";position:absolute;left:50%;bottom:-7px;width:12px;height:12px;background:var(--white);border-right:1px solid var(--line);border-bottom:1px solid var(--line);transform:translateX(-50%) rotate(45deg)}
.tab.solid{background:var(--blue);color:var(--white)}
.protect-title{left:163px;top:1160px;font-size:13.5px;color:var(--muted)}
p.copy.protect-copy{left:163px;top:1186px;width:358px;text-align:justify;font-size:10.2px;letter-spacing:-.15px}
.photo-handshake{left:538px;top:1196px;width:201px;height:255px}
.photo-handshake div{background:linear-gradient(135deg,#e6e6e6,#b89c86 50%,#2d3a4f)}
.coverage-title{left:163px;top:1468px;width:560px;font-weight:700;font-size:15px;color:var(--heading);line-height:19px}
.coverage{top:1514px;list-style:none}
.coverage li{font-size:11.5px;color:var(--link);line-height:24px;display:flex;align-items:flex-start;gap:13px}
.coverage li::before{content:"\203A";color:#333;font-size:14px;line-height:24px;width:8px;flex:none}
.cov-left{left:163px}
.cov-right{left:453px;width:260px}
.box{border:1px solid var(--line);background:var(--white)}
.about{left:763px;top:902px;width:280px;height:368px;padding:20px 21px}
.about .copy{font-size:10.6px;line-height:19.2px;margin-top:12px;text-align:justify}
.contact{left:763px;top:1285px;width:280px;height:511px;padding:20px 21px 0}
.contact .copy{font-size:11px;line-height:19.2px;margin-top:8px}
.contact-row{display:flex;gap:12px;font-size:11px;line-height:19px;margin-top:10px}
.contact-row svg{flex:none;margin-top:3px}
.map{left:763px;top:1524px;width:280px;height:272px;background:linear-gradient(135deg,#eceae6,#dfe3e6 60%,#b7d0f0)}
.footer{left:0;top:1831px;width:1200px;height:340px;background:var(--blue)}
.footer h3{font-weight:400;font-size:19px;color:var(--white)}
.quick-links{left:169px;top:28px}
.quick-links ul{list-style:none;margin-top:18px}
.quick-links li{color:var(--white);font-size:11.5px;height:29px;display:flex;gap:14px}
.quick-links li::before{content:"\203A";font-size:14px;line-height:13px}
.socials{left:176px;top:268px;display:flex;gap:6px}
.socials span{width:22px;height:22px;background:var(--white);border:2px solid #2b7fc0}
.copyright{left:170px;top:306px;color:var(--white);font-size:10px}
.quote-title{left:408px;top:28px;width:636px;text-align:center}
.field{background:var(--white);height:32px;font-size:10px;color:#555;padding:10px 14px}
.attach{display:flex;justify-content:space-between;align-items:center;padding:0 10px 0 18px}
.attach span.browse{background:#9a9a9a;color:var(--white);padding:5px 24px;font-size:10px}
.comments{height:49px}
.submit{background:var(--olive);color:var(--white);font-size:15px;display:flex;align-items:center;justify-content:center;letter-spacing:.5px}
</style>
</head>
<body>

<header class="hero abs">
  <div class="hero-photo" role="img" aria-label="Photo of a smiling family running across a lawn in front of their house"></div>
  <svg class="hero-waves" width="1200" height="620" viewBox="0 0 1200 620" aria-hidden="true">
    <path d="M560 565 C780 525 1000 470 1200 415 L1200 485 C1000 545 800 590 560 600 Z" fill="#7b9a2c"/>
    <path d="M0 440 C150 425 300 445 450 505 C620 565 850 575 1200 478 L1200 560 C900 640 640 640 450 585 C300 535 150 505 0 495 Z" fill="#0b5d95"/>
    <path d="M0 495 C150 505 300 535 450 585 C640 640 900 640 1200 560 L1200 620 L0 620 Z" fill="#ffffff"/>
  </svg>
</header>

<div class="brand abs">
  <span class="brand-mark"></span>
  <span class="brand-name">Corvella Insurance Group</span>
</div>

<nav class="nav abs">
  <a class="active">Home</a><a>About Us</a><a>Services</a><a>Products</a><a>Blog</a><a>Contact Us</a>
  <span class="search"><svg width="12" height="12" viewBox="0 0 12 12"><circle cx="5" cy="5" r="3.5" fill="none" stroke="#111" stroke-width="1.8"/><line x1="7.5" y1="7.5" x2="11" y2="11" stroke="#111" stroke-width="2"/></svg></span>
</nav>

<div class="callout abs">
  <div class="lead">Call Today for Your</div>
  <div class="sub">no obligation insurance analysis</div>
  <div class="phone">
    <svg width="22" height="22" viewBox="0 0 24 24"><path d="M6.6 10.8a15 15 0 0 0 6.6 6.6l2.2-2.2a1 1 0 0 1 1-.25 11.4 11.4 0 0 0 3.6.6 1 1 0 0 1 1 1V20a1 1 0 0 1-1 1A17 17 0 0 1 3 4a1 1 0 0 1 1-1h3.5a1 1 0 0 1 1 1c0 1.250.2 2.45.6 3.6a1 1 0 0 1-.25 1z" fill="#fff"/></svg>
    (555) 014 - 2290
  </div>
</div>

<div class="tilt tilt-family abs"><div role="img" aria-label="Photo of a family lying together and smiling"></div></div>
<div class="tilt tilt-car abs"><div role="img" aria-label="Photo of hands holding a small green model car"></div></div>

<section class="welcome abs">
  <h2 class="section-title">WELCOME TO OUR CIG</h2>
  <p class="copy">Corvella Insurance Group has joined with regional &amp; national insurance companies to provide quality products and superior service. We take the time to discuss options and coverages, not to just sell insurance products. We strive to educate you in the decision making process to become an informed consumer.<br>We specialize in commercial business &amp; personal insurance. We are committed to providing personal attention to all your insurance needs.</p>
  <span class="btn">Read more</span>
</section>

<div class="framed photo-couple abs"><div role="img" aria-label="Photo of a couple reviewing insurance documents at home"></div></div>

<section class="products abs">
  <h2 class="section-title">PRODUCTS AND SERVICES</h2>
  <p class="copy">Corvella Insurance Group is a one stop shop for all of your personal and business insurance needs. With our established relationships and market knowledge, we will tailor an insurance program specifically designed to meet your needs. As an independent insurance agency, we are able to provide you with a wide variety of plans and carriers. Corvella Insurance Group represents top insurance carriers in the marketplace.</p>
  <p class="prompt">Click a link below to learn more about the different types of insurance we offer.</p>
  <div class="tabs">
    <span class="tab outline">Business Insurance</span>
    <span class="tab solid">Personal Insurance</span>
  </div>
</section>

<p class="protect-title abs">Protecting Your Business is Our Priority.</p>
<p class="copy protect-copy abs">Corvella Insurance Group can help you take steps to protect your business and your family from the financial consequences of events that could disrupt operations, reduce profits, or even cause the business to go bankrupt.<br>We know what questions to ask, what risks need to be identified, and most importantly, we understand how to best insure them. Business insurance is a risk management tool that enables businesses to transfer the risk of a loss to an insurance company. Business insurance protects your business against the possibility of sustaining a much larger financial loss. All businesses need to insure against risks—such as fire, theft, natural disaster, legal liability, automobile accidents, and the death or disability of key employees—but it is especially important for small business owners. Your life savings may be tied up in the company.</p>

<div class="framed photo-handshake abs"><div role="img" aria-label="Photo of two businessmen shaking hands"></div></div>

<h3 class="coverage-title abs">Corvella Insurance Group provides the following types of business insurance coverage:</h3>
<ul class="coverage cov-left abs">
  <li>Bond</li><li>Builders Risk</li><li>Business Owners Policy (BOP)</li><li>Commercial Auto</li><li>Crime</li><li>Crop / Hail</li><li>Difference in Conditions</li><li>Directors and Officers (D&amp;O)</li><li>Employment Practices Liability</li><li>Errors &amp; Omissions (E&amp;O)</li><li>Equipment Breakdown</li><li>Garage</li>
</ul>
<ul class="coverage cov-right abs">
  <li>General Liability</li><li>Inland Marine</li><li>Liquor Liability</li><li>Medical Malpractice</li><li>Owners and Contractors Protective Liability (OCP)</li><li>Professional Liability</li><li>Property</li><li>Truckers</li><li>Umbrella</li>
</ul>

<aside class="box about abs">
  <h2 class="section-title">ABOUT US</h2>
  <p class="copy">Established in 2015, Corvella Insurance Group is a full service independent insurance agency. Our licensed agents have the experience to custom tailor a program to meet your specific needs &amp; our professional support staff will provide you with top notch customer service to help ease the burden of managing your insurance program.<br>We have established relationships with carriers in order to offer you the most competitive products and services available in the marketplace today.<br>We look forward to working with you!</p>
</aside>

<aside class="box contact abs">
  <h2 class="section-title">CONTACT US</h2>
  <p class="copy">We are located in the Lakeview Commerce Park in Coral Bay, Florida</p>
  <div class="contact-row" style="margin-top:14px">
    <svg width="9" height="13" viewBox="0 0 9 13"><path d="M4.5 0A4.5 4.5 0 0 0 0 4.5C0 8 4.5 13 4.5 13S9 8 9 4.5A4.5 4.5 0 0 0 4.5 0zm0 6.3a1.8 1.8 0 1 1 0-3.6 1.8 1.8 0 0 1 0 3.6z" fill="#333"/></svg>
    <span>1820 Harbor Point Drive, Suite 210<br>Coral Bay, FL 30155</span>
  </div>
  <div class="contact-row" style="margin-top:16px">
    <svg width="10" height="10" viewBox="0 0 24 24"><path d="M6.6 10.8a15 15 0 0 0 6.6 6.6l2.2-2.2a1 1 0 0 1 1-.25 11.4 11.4 0 0 0 3.6.6 1 1 0 0 1 1 1V20a1 1 0 0 1-1 1A17 17 0 0 1 3 4a1 1 0 0 1 1-1h3.5a1 1 0 0 1 1 1c0 1.25.2 2.45.6 3.6a1 1 0 0 1-.25 1z" fill="#333"/></svg>
    <span>Phone: (555)&nbsp;&nbsp;&nbsp;-</span>
  </div>
  <div class="contact-row" style="margin-top:2px">
    <svg width="11" height="11" viewBox="0 0 11 11"><rect x="0" y="3" width="11" height="6" fill="#333"/><rect x="2" y="0" width="7" height="3" fill="#333"/><rect x="2" y="7" width="7" height="4" fill="#333"/></svg>
    <span>Fax: (555) 017-4411</span>
  </div>
</aside>

<div class="map abs" role="img" aria-label="Street map showing the office location"></div>

<footer class="footer abs">
  <div class="quick-links abs">
    <h3>Quick Links</h3>
    <ul><li>Home</li><li>About Us</li><li>Services</li><li>Products</li><li>Blog</li><li>Contact Us</li></ul>
  </div>
  <div class="socials abs"><span></span><span></span><span></span><span></span><span></span></div>
  <p class="copyright abs">© www.corvellagroup.com</p>

  <h3 class="quote-title abs">Quick Contact / Get a Quote</h3>
  <div class="field abs" style="left:408px;top:71px;width:205px">Name</div>
  <div class="field abs" style="left:624px;top:71px;width:205px">Company</div>
  <div class="field abs" style="left:840px;top:71px;width:205px">Street Address</div>
  <div class="field abs" style="left:408px;top:112px;width:205px">Address</div>
  <div class="field abs" style="left:624px;top:112px;width:205px">Address Line 2</div>
  <div class="field abs" style="left:840px;top:112px;width:205px">City</div>
  <div class="field abs" style="left:408px;top:153px;width:205px">State</div>
  <div class="field abs" style="left:624px;top:153px;width:205px">Zip</div>
  <div class="field abs" style="left:840px;top:153px;width:205px">Phone</div>
  <div class="field attach abs" style="left:408px;top:195px;width:421px"><span>Send Attachments</span><span class="browse">Browse</span></div>
  <div class="field abs" style="left:840px;top:195px;width:205px">Email Address</div>
  <div class="field comments abs" style="left:408px;top:236px;width:421px">Comments or Questions</div>
  <div class="submit abs" style="left:840px;top:236px;width:205px;height:51px">SUBMIT</div>
</footer>

</body>
</html>
```